Moldran Foods needs a new label for canned pineapple

We want a very tasty (in terms of making your mouth water) and clean design (less is more) for our canned pineapple under the new logo of Moldran Leafline division

Target Market(s)

The company’s mission is to bring quality food to target audiences of any social status (you receive a bit more than what you spend). Our core values are: reliability, loyalty and commitment to development.
The product is sold to mainstream and lower Mainstream customers.

Requirements
Must have
• The design should take into consideration the visibility on the shelf among competitor products (brief file) and that the product is a MAINSTREAM product.
We want a very tasty (in terms of making your mouth water) and clean design (less is more). The design should be easily modifiable for other canned fruits or vegetables.
The package must display on the front the following elements listed in the order of their should have noticeability:
• Moldran Leaf logo
• Pineapple picture
• Product name
Designers should take into account that the shelfs for displaying the products in the shops may have an elevation of up to 3 cm that can overlap the product label.

Guidelines
• We would like the packaging to be as simple as possible (or at least not to sabotage the Moldran name ), as our strategy depends on the agressive communication of the Moldran logo.
• We would also like to communicate through suggestive and optimal colours as to be easily spotted on the shelf.
• As we have quite a minimal communication budget we need basically for the packaging to do a lot of the communication job itself
• FMCG is a highly visual industry so we have to include pictures of the products on the packages (even more than others do, as we are focused on health and quality - we want people to have that feeling of fresh products even though we are selling canned ones)
Should not have
• but the minimum amount of text on the front.

```html
<!DOCTYPE html>
<html lang="ro">
<head>
<meta charset="utf-8">
<title>Moldran Leafline – Ananas felii</title>
<link rel="stylesheet" href="https://fonts.googleapis.com/css2?family=Bebas+Neue&family=Lato:wght@400;700&display=swap">
<style>
  :root {
    --backdrop-top: #ececec;
    --backdrop-bottom: #c4c4c4;
    --label-white: #ffffff;
    --brand-green: #2f8a3e;
    --pineapple-deep: #e8d83e;
    --pineapple-light: #f6f0b4;
    --title-ink: #1d1d1b;
    --title-soft: #6a6a68;
    --subtitle-olive: #a89b4e;
    --info-ink: #3a3a3a;
  }
  * { box-sizing: border-box; margin: 0; padding: 0; }
  html, body { width: 1200px; height: 900px; overflow: hidden; }
  body {
    background: linear-gradient(to bottom, var(--backdrop-top), var(--backdrop-bottom));
    position: relative;
    font-family: "Lato", sans-serif;
  }
  .label {
    position: absolute;
    left: 455px; top: 268px;
    width: 320px; height: 392px;
    background: var(--label-white);
  }
  .brand {
    position: absolute;
    left: 0; right: 0; top: 40px;
    display: flex; align-items: center; justify-content: center; gap: 8px;
  }
  .brand-dot {
    width: 14px; height: 14px; border-radius: 50%;
    background: var(--brand-green);
  }
  .brand-name {
    font-family: "Lato", sans-serif;
    font-weight: 700;
    font-size: 20px;
    color: var(--brand-green);
  }
  .pineapple-slice {
    position: absolute;
    left: 31px; top: 128px;
    width: 244px; height: 244px;
  }
  .product-name {
    position: absolute;
    left: 58px; top: 228px;
    font-family: "Bebas Neue", sans-serif;
    font-size: 50px;
    letter-spacing: 4px;
    line-height: 1;
    color: var(--title-ink);
    white-space: nowrap;
  }
  .product-name .soft { color: var(--title-soft); }
  .product-variant {
    position: absolute;
    left: 102px; top: 268px;
    font-size: 13px;
    color: var(--subtitle-olive);
    white-space: nowrap;
  }
  .net-weight {
    position: absolute;
    right: 6px; top: 316px;
    font-size: 12px;
    line-height: 1.3;
    text-align: center;
    color: var(--info-ink);
  }
</style>
</head>
<body>
  <main class="label">
    <div class="brand">
      <span class="brand-dot"></span>
      <span class="brand-name">Moldran Leafline</span>
    </div>

    <svg class="pineapple-slice" viewBox="0 0 244 244" role="img" aria-label="Pineapple ring slice">
      <defs>
        <linearGradient id="slice-tone" x1="0" y1="0" x2="1" y2="0">
          <stop offset="0" stop-color="var(--pineapple-deep)"/>
          <stop offset="0.45" stop-color="var(--pineapple-light)"/>
          <stop offset="1" stop-color="var(--pineapple-deep)"/>
        </linearGradient>
      </defs>
      <path fill="url(#slice-tone)" fill-rule="evenodd"
            d="M122 0a122 122 0 1 0 0.01 0Z M122 64a58 58 0 1 0 0.01 0Z"/>
    </svg>

    <h1 class="product-name">AN<span class="soft">ANAS</span> FELII</h1>
    <p class="product-variant">in suc indulcit</p>
    <p class="net-weight">298 g ℮<br>175g<br>(uscat)</p>
  </main>
</body>
</html>
```